Need to drive pregnant women to my 3d4d ultrasound studio where i provide 4d ultrasound with hyperalistic imaging and gender reveals

Industry/Entity Type

Healthcare

Font styles to use
Decorative
Script

Requirements
Must have
• My Company name Cielo de Nuestra Espera 4D. EVERYTHING HAS TO BE IN SPANISH
Nice to have
• SIMPLE AND NOT TOO BUSY
Should not have
• website

```html
<!DOCTYPE html>
<html lang="es">
<head>
<meta charset="UTF-8">
<title>Cielo de Nuestra Espera 4D – Banner</title>
<link href="https://fonts.googleapis.com/css2?family=Roboto:wght@300;700&family=Dancing+Script:wght@500&display=swap" rel="stylesheet">
<style>
  :root {
    --backdrop: #a0a0a0;
    --panel-dark: #000000;
    --panel-sheen: #3e3e40;
    --panel-light: #ffffff;
    --text-light: #ffffff;
    --text-dark: #000000;
    --scan-dark: #3a1c06;
    --scan-mid: #b5661e;
    --scan-light: #d98a3a;
    --baby-dark: #b57a6a;
    --baby-light: #f0c4b0;
  }
  * { margin: 0; padding: 0; box-sizing: border-box; }
  html, body {
    width: 1200px;
    height: 600px;
    overflow: hidden;
    background: var(--backdrop);
    font-family: "Roboto", Arial, sans-serif;
  }
  .banner {
    position: absolute;
    left: 79px;
    top: 154px;
    width: 1043px;
    height: 304px;
    display: flex;
    box-shadow: 1px 2px 3px rgba(0, 0, 0, 0.35);
  }
  .banner__message {
    width: 603px;
    height: 100%;
    background:
      linear-gradient(118deg, var(--panel-dark) 0%, var(--panel-dark) 30%, var(--panel-sheen) 55%, var(--panel-dark) 80%, var(--panel-dark) 100%);
    position: relative;
    color: var(--text-light);
  }
  .banner__title {
    position: absolute;
    left: 69px;
    top: 44px;
    font-weight: 700;
    font-size: 52px;
    line-height: 1;
    letter-spacing: 0.5px;
    text-transform: uppercase;
    white-space: nowrap;
  }
  .banner__title-highlight {
    position: absolute;
    left: 71px;
    top: 105px;
    height: 59px;
    padding: 0 13px 0 14px;
    background: var(--panel-light);
    color: var(--text-dark);
    font-weight: 700;
    font-size: 52px;
    line-height: 59px;
    text-transform: uppercase;
    white-space: nowrap;
  }
  .banner__tagline {
    position: absolute;
    left: 69px;
    top: 184px;
    font-family: "Dancing Script", "Brush Script MT", cursive;
    font-weight: 500;
    font-size: 34px;
    line-height: 40px;
    color: var(--text-light);
    white-space: nowrap;
  }
  .banner__gallery {
    flex: 1;
    background: var(--panel-light);
    position: relative;
  }
  .gallery__photo {
    position: absolute;
    top: 31px;
    width: 185px;
    height: 243px;
  }
  .gallery__photo--scan {
    left: 34px;
    background: radial-gradient(ellipse at 45% 55%, var(--scan-light) 0%, var(--scan-mid) 45%, var(--scan-dark) 100%);
  }
  .gallery__photo--newborn {
    left: 221px;
    background: radial-gradient(ellipse at 45% 55%, var(--baby-light) 0%, #e0a897 55%, var(--baby-dark) 100%);
  }
</style>
</head>
<body>
  <section class="banner">
    <div class="banner__message">
      <h1 class="banner__title">Cielo de Nuestra</h1>
      <div class="banner__title-highlight">Espera 4D</div>
      <p class="banner__tagline">Ecografía 4D hiperrealista<br>y revelación de género</p>
    </div>
    <div class="banner__gallery">
      <div class="gallery__photo gallery__photo--scan" role="img" aria-label="Imagen de ecografía 4D en tonos ámbar de un bebé en el vientre"></div>
      <div class="gallery__photo gallery__photo--newborn" role="img" aria-label="Fotografía de un recién nacido dormido"></div>
    </div>
  </section>
</body>
</html>
```